Wordpress Design For Financial Investment Company

//** NEW WIREFRAME ADDED TO HELP WITH LAYOUT ISSUES. PLEASE REFER TO WIREFRAME IN ATTACHED FILES. NO DESIGN WILL BE CONSIDERED IF IT DOES NOT FOLLOW THE WIREFRAME. **//
//** PLEASE READ THE ENTIRE BRIEF INCLUDING ALL UPDATES TO THE BRIEF. THE CLIENT IS VERY SPECIFIC ABOUT WHAT THEY WANT AND I'VE COVERED SEVERAL THINGS IN THE UPDATES. THERE IS ALSO A VIDEO UPDATE THAT HAS SOME VALUABLE INFORMATION IN IT FOR THIS CONTEST. **//
The client is an investment advisor who needs a new website designed. The current site is http://www.velmorhold.example.
The client wants the site to be green to match the attached logo.
The home page should have relevant images in the rotator. No people hugging! This is a financial investment site, not a family counseling site.
Also, the client wants 4 buttons on the home page to highlight the 4 main areas they focus on:
Investment Advice and Education
General Financial Planning
Retirement Planning
401K Planning
The top right area of the site needs to have their phone number, a call to action, and 2 buttons.
Their phone number is 303-418-7719
The call to action should say something like "Call for a free consultation!"
The buttons need to say:
Login To Your Brokavell Account
Login To Your Quillbrook Account
The final design should communicate professionalism, financial safety and growth.
Main navigation should be:
Home
About Us
Associates
Services
Contact
Mission Statement (Could also be "Our Mission")
This is a site that the client likes: http://www.pkwadvisoryfirm.example/
Updates
The designs should not have:
Newsletter content. A newsletter sign up is fine
Learning Center
Calculators
Stock prices/tickers
The design should have a contact form on the page.
I have talked to my client and have some updates. I did a video update because I thought it would be easier to show what I'm trying to get across.
Reason: I am going to be extending the contest a few more days. I'm still not getting quite what I want and very few people are even trying to follow the creative brief and the updates to it.
PLEASE read the entire brief and the updates. There is also a video I made that explains everything. I've also attached a wireframe.
Thanks!
Target Market(s)
People looking for a high-end financial investment company.
Industry/Entity Type
Investment
Requirements
Must have
- !!FOLLOW THE WIREFRAME FOR LAYOUT!!
!!THEIR LOGO!!
4 buttons to highlight their main practice areas
Phone number in the top right
"Free Consultation" call to action
2 Login buttons in the top right
A contact form on the page.
Should not have
- The designs should not have:
Learning Center
Calculators
Stock prices/tickers

```html
<!DOCTYPE html>
<html lang="en">
<head>
<meta charset="utf-8">
<title>Velmor Financial</title>
<link href="https://fonts.googleapis.com/css2?family=Mulish:wght@400;600;700&family=Questrial&display=swap" rel="stylesheet">
<style>
:root{
  --teal:#139e93;
  --teal-dark:#0d8479;
  --teal-text:#118a80;
  --ink:#2a2a2a;
  --muted:#8a8a8a;
  --body:#6b6b6b;
  --rule:#e2e2e2;
  --panel:#f4f4f4;
  --backdrop:#6f6f6f;
  --footer:#2f2f2f;
  --footer-bar:#262626;
  --footer-text:#a9a9a9;
  --brown:#4a2c22;
}
*{box-sizing:border-box;margin:0;padding:0}
html,body{width:861px;height:1200px;overflow:hidden}
body{background:var(--backdrop);font-family:"Mulish",sans-serif;color:var(--body);position:relative}
.abs{position:absolute}
.sheet{left:78px;top:29px;width:704px;height:955px;background:#fff;box-shadow:0 0 6px rgba(0,0,0,.35)}
/* header */
.logins{left:426px;top:30px;width:340px;height:25px;background:#1f1f1f;border-radius:0 0 3px 3px;display:flex;align-items:center;font-size:9px;color:#fff}
.logins span{flex:1;text-align:center}
.logins i{width:2px;height:17px;background:#fff}
.brand{left:112px;top:70px;display:flex;align-items:center;gap:8px;font-family:"Questrial",sans-serif;font-size:17px;color:var(--brown)}
.brand b{width:14px;height:14px;border-radius:50%;background:var(--brown);display:block}
.call{left:630px;top:77px;display:flex;gap:5px;font-family:"Questrial",sans-serif}
.call p{font-size:12px;line-height:15px;color:var(--brown)}
.phone{left:633px;top:109px;font-family:"Questrial",sans-serif;font-size:20px;color:#222}
/* nav */
.nav{left:70px;top:140px;width:720px;height:35px;background:linear-gradient(#1bb0a4,var(--teal-dark));box-shadow:0 2px 3px rgba(0,0,0,.3);font-size:10.5px;font-weight:600;color:#fff}
.nav span{position:absolute;top:11px}
.nav .on{top:6px;left:32px;background:#1c1c1c;border-radius:4px;padding:5px 13px;font-size:11px}
/* hero */
.hero{left:86px;top:174px;width:691px;height:302px;background:linear-gradient(100deg,#c5b199 0%,#9c8268 35%,#d8c1a6 55%,#8f7b68 80%,#b6a48f 100%)}
.claim{left:86px;top:353px;width:294px;height:88px;background:rgba(255,255,255,.72);border-radius:0 8px 8px 0;padding:4px 10px;font-family:"Questrial",sans-serif;font-size:21px;line-height:28px;letter-spacing:-.8px;color:#555}
.claim em{font-style:normal;color:var(--brown)}
.dots{left:104px;top:455px;display:flex;gap:5px}
.dots i{width:4px;height:4px;border-radius:50%;background:#fff}
.dots i:first-child{background:var(--teal)}
/* services */
.services{left:86px;top:476px;width:691px;height:154px;display:flex;background:var(--panel);border-bottom:1px solid var(--rule)}
.svc{flex:1;text-align:center;padding-top:16px;border-right:1px solid var(--rule)}
.svc h3{font-weight:400;font-size:11px;color:#222;margin:7px 0 8px}
.svc p{font-size:8.6px;line-height:13px;color:var(--muted);padding:0 14px}
.svc.active{background:linear-gradient(#3a3a3a,#111);}
.svc.active h3,.svc.active p{color:#fff;font-weight:700}
/* welcome */
.welcome{left:110px;top:655px;width:645px}
.welcome h2{font-family:"Questrial",sans-serif;font-weight:400;font-size:19px;color:var(--teal-text);margin-bottom:14px}
.welcome p{font-size:8.6px;line-height:15.2px;color:var(--body)}
.welcome a,.more{color:var(--teal-dark);text-decoration:none}
.divider{left:86px;top:781px;width:691px;height:1px;background:var(--rule)}
.col h2{font-family:"Questrial",sans-serif;font-weight:400;font-size:16px;color:#333}
.ql-item{display:flex;gap:8px;align-items:flex-start}
.ql-item h4{font-family:"Questrial",sans-serif;font-weight:400;font-size:13px;color:var(--teal-text)}
.ql-item p{font-size:8.4px;line-height:13px;color:var(--body);margin-top:4px}
.ql-item p b{color:#222;font-weight:600}
.event{display:flex;gap:8px;padding:6px 0;border-bottom:1px solid var(--rule);width:164px}
.thumb{width:37px;height:37px;background:linear-gradient(135deg,#d8cfc4,#8f8175);border:2px solid #eee;flex:none}
.event h5{font-weight:600;font-size:8.6px;color:var(--teal-text)}
.event p{font-size:7.6px;color:#999;line-height:12px}
.event em{font-family:Georgia,serif;font-size:7.6px;color:#888}
/* footer */
.footer{left:78px;top:984px;width:704px;height:160px;background:var(--footer)}
.fcol h2{font-family:"Questrial",sans-serif;font-weight:400;font-size:14px;color:#f1f1f1;margin-bottom:9px}
.fcol p{font-size:7.6px;line-height:13px;letter-spacing:.4px;color:var(--footer-text)}
.fcol .who{color:var(--teal)}
.email{width:143px;height:22px;background:#fff;border-radius:3px;font-size:8px;color:#aaa;padding:6px 10px;margin-top:10px}
.sub{margin-top:13px;display:inline-block;background:linear-gradient(#fff,#ddd);border-radius:3px;font-size:8px;font-weight:700;color:#222;padding:4px 12px}
.bar{left:78px;top:1144px;width:704px;height:28px;background:var(--footer-bar);font-size:8.4px;color:#eee}
.bar .copy{position:absolute;left:23px;top:9px}
.bar .links{position:absolute;right:17px;top:9px;display:flex;gap:11px}
</style>
</head>
<body>
<div class="abs sheet"></div>

<div class="abs logins"><span>Login To Your Brokavell Account</span><i></i><span>Login To Your Quillbrook Account</span></div>
<div class="abs brand"><b></b>Velmor Financial, Inc.</div>
<div class="abs call">
  <svg width="26" height="28" viewBox="0 0 26 28"><path d="M4 15a9 9 0 0 1 18 0" fill="none" stroke="#333" stroke-width="2.2"/><rect x="2" y="14" width="5" height="8" rx="2" fill="#333"/><rect x="19" y="14" width="5" height="8" rx="2" fill="#333"/><path d="M21 22c0 3-4 4-8 4" fill="none" stroke="#333" stroke-width="1.4"/></svg>
  <p>Call for a<br>free Consultation!</p>
</div>
<div class="abs phone">303-418-7719</div>

<nav class="abs nav">
  <span class="on">Home</span>
  <span style="left:133px">About Us</span>
  <span style="left:247px">Associates</span>
  <span style="left:367px">Services</span>
  <span style="left:478px">Contact</span>
  <span style="left:585px">Mission Statement</span>
</nav>

<div class="abs hero" role="img" aria-label="Smiling senior couple seated together in a library"></div>
<div class="abs claim">Only 42% of americans know how much money to save for <em>RETIREMENT.</em></div>
<div class="abs dots"><i></i><i></i><i></i><i></i><i></i></div>

<section class="abs services">
  <div class="svc">
    <svg width="26" height="40" viewBox="0 0 26 40"><circle cx="17" cy="3" r="2.5" fill="#222"/><circle cx="10" cy="7" r="1.6" fill="#222"/><path d="M10 12h6v8l8 17H2l8-17z" fill="#222"/></svg>
    <h3>Investment Advice &amp; Education</h3>
    <p>Lorem ipsum dolor sit amet, consectetuer adipiscing elit, sed diam nonummy nibh euismod tincidunt ut laoreet.</p>
  </div>
  <div class="svc active">
    <svg width="40" height="40" viewBox="0 0 40 40"><path d="M37 3 18 24l-3-3z" fill="#fff"/><path d="M14 22c-6 0-7 6-7 8 0 3-3 4-4 4 5 3 14 1 14-8z" fill="#fff"/></svg>
    <h3>401K Planning</h3>
    <p>Le Lorem Ipsum est simplement du faux texte employé dans la composition et la mise en page avant impression.</p>
  </div>
  <div class="svc">
    <svg width="26" height="40" viewBox="0 0 26 40"><path d="M13 2a11 11 0 0 0-6 20v6h12v-6A11 11 0 0 0 13 2z" fill="#222"/><path d="M9 10l4 10 4-10" fill="none" stroke="#fff" stroke-width="1.3"/><rect x="8" y="30" width="10" height="3" fill="#222"/><rect x="9" y="34" width="8" height="3" rx="1.5" fill="#222"/></svg>
    <h3>General Financial Planning</h3>
    <p>Lorem ipsum dolor sit amet, consectetuer adipiscing elit, sed diam nonummy nibh euismod tincidunt ut laoreet.</p>
  </div>
  <div class="svc" style="border-right:0">
    <svg width="36" height="40" viewBox="0 0 36 40"><rect x="2" y="2" width="32" height="36" rx="3" fill="none" stroke="#222" stroke-width="2.5"/><rect x="7" y="7" width="22" height="24" fill="none" stroke="#222" stroke-width="1.4"/><circle cx="18" cy="34" r="1.4" fill="#222"/></svg>
    <h3>Retirement Planning</h3>
    <p>Lorem ipsum dolor sit amet, consectetuer adipiscing elit, sed diam nonummy nibh euismod tincidunt ut laoreet.</p>
  </div>
</section>

<section class="abs welcome">
  <h2>WELCOME TO VELMOR</h2>
  <p>Le Lorem Ipsum est simplement du faux texte employé dans la composition et la mise en page avant impression. Le Lorem Ipsum est le faux texte standard de l'imprimerie depuis les années 1500, quand un peintre anonyme assembla ensemble des morceaux de texte pour réaliser un livre spécimen de polices de texte. Il n'a pas fait que survivre cinq siècles, mais s'est aussi adapté à la bureautique informatique, sans que son contenu n'en soit modifié. Il a été popularisé dans les années 1960 grâce à la vente de feuilles. <a href="#">Read More</a></p>
</section>
<div class="abs divider"></div>

<section class="abs col" style="left:107px;top:806px;width:262px">
  <h2>Quick Links</h2>
  <div class="ql-item" style="margin-top:10px">
    <svg width="14" height="14" viewBox="0 0 14 14" style="flex:none;margin-top:2px"><circle cx="7" cy="7" r="7" fill="#333"/><rect x="3.5" y="6.2" width="7" height="1.6" fill="#fff"/></svg>
    <div><h4>Our Firm</h4><p>Lorem ipsum dolor sit amet, consectetuer adipiscing elit, sed diam nonummy nibh euismod tincidunt ut laoreet dolore magna aliquam erat volutpat. Ut wisi enim ad minim veniam. &nbsp;<b>Read More</b></p></div>
  </div>
  <div style="margin:8px 0 0 21px;border-top:1px solid var(--rule)"></div>
  <div class="ql-item" style="margin-top:6px">
    <svg width="14" height="14" viewBox="0 0 14 14" style="flex:none;margin-top:2px"><circle cx="7" cy="7" r="7" fill="#333"/><rect x="3.5" y="6.2" width="7" height="1.6" fill="#fff"/><rect x="6.2" y="3.5" width="1.6" height="7" fill="#fff"/></svg>
    <h4>Mission Statement and Core Values</h4>
  </div>
  <div style="margin:6px 0 0 21px;border-top:1px solid var(--rule)"></div>
</section>

<section class="abs col" style="left:392px;top:806px">
  <h2>Events</h2>
  <div class="event" style="margin-top:6px"><div class="thumb" role="img" aria-label="Portrait photo of a young child"></div><div><h5>Anteposuerit litterarum</h5><p>est usus legentis in iis.</p><em>Jan 07, 2012</em></div></div>
  <div class="event"><div class="thumb" role="img" aria-label="Photo of a parent with a child"></div><div><h5>Anteposuerit litterarum</h5><p>est usus legentis in iis.</p><em>Jan 06, 2012</em></div></div>
</section>

<section class="abs col" style="left:574px;top:806px;width:180px">
  <h2>Recent News</h2>
  <div style="display:flex;gap:10px;margin-top:8px">
    <div style="text-align:center;font-family:'Questrial',sans-serif;color:#222;line-height:11px">
      <div style="font-size:16px;line-height:18px">20<sup style="font-size:7px">th</sup></div>
      <div style="font-size:12px">FEB</div><div style="font-size:8px">2013</div>
    </div>
    <div>
      <div class="ql-item"><h4>Vulputate velit esse molestie.</h4></div>
      <p style="font-size:8.4px;line-height:13px;margin-top:4px">Lorem ipsum dolor sit consectetuer adipiscing elit, sed diam nonummy nibh euismod tincidunt ut laoreet dolore magna aliquam rat volutpat. Ut wisi enim ad minim, qis nostrud exerci... &nbsp;<b style="color:#222;font-weight:600">Read More</b></p>
    </div>
  </div>
</section>

<footer class="abs footer">
  <div class="abs fcol" style="left:29px;top:26px">
    <h2>Contact Details</h2>
    <p>482 Larkspur Ave #210<br>Brookfield Terrace, CO 80990</p>
    <p style="margin-top:6px">Phone: 303-418-7719 800-555-0148<br>Fax: 303-555-0172</p>
    <p style="margin-top:6px">Dana @velmorfinancial.example<br>Map and Directions</p>
  </div>
  <div class="abs fcol" style="left:235px;top:26px">
    <h2>SiteMap</h2>
    <p>Our Associates<br>Our Location<br>Our Services<br>Our Qualifications<br>Our Articles<br>External Page<br>Tell A Friend</p>
  </div>
  <div class="abs fcol" style="left:356px;top:26px;width:150px">
    <h2>Testimonials</h2>
    <p>Lorem Ipsum est simplement du fauxtexte employé.</p><p class="who">Corwin Hale</p>
    <p style="margin-top:12px">Lorem Ipsum est simplement du fauxtexte employé.</p><p class="who">Anonymus</p>
  </div>
  <div class="abs fcol" style="left:534px;top:26px;width:160px">
    <h2>Sign Up for Newsletter</h2>
    <p>Lorem Ipsum est simplement du fauxtexte employé</p>
    <div class="email">Email Address</div>
    <span class="sub">Subscribe</span>
  </div>
</footer>
<div class="abs bar">
  <span class="copy">© Velmor. All rights reserved.</span>
  <span class="links"><span>Home</span><span>About Us</span><span>Associates</span><span>Services</span><span>Contact</span><span>Mission Statement</span></span>
</div>
</body>
</html>
```